The design should look similar to the uploaded example to accommodate the information needed for a business card template. I would like to see the colors orange and charcoal grey incorporated along with the logo.The following should be on the back of the card SPECIALIZING IN NEW AND USED TIRES & WHEELS FOR:- Loaders- Skid Steers- Telehandlers- Boom Lifts- Forklifs and moreELIMINATING DOWNTIMEWheel Exchange Program for New & Used Foam Filled and Solid Rubber TiresSPECIALTY SERVICES- Foam Filling Tires- Largest Tire Press in SE- ONSITE Forklift Tire Press- Boom Truck Services - Rubber Tracks

Target Market(s)

New and Existing Customers

Industry/Entity Type

Business

Contact Information for Business Card

NAMEHEAVY DUTY TIRE, LLC8470 Belvedere RoadWest Palm Beach, FL 33411P: 844-HD-TIRESF: 561-431-6469C:E: W: WWW.GRANITERIMSUPPLY-EXAMPLE.COM

Font styles to use
Sans Serif

Colors
f37122
333333

Requirements
Must have
• The logo and the information indicated for the backside of the card
Nice to have
• Keep the orange and charcoal grey colors

```html
<!DOCTYPE html>
<html lang="en">
<head>
<meta charset="utf-8">
<title>Granite Rim Supply – Business Card</title>
<link rel="stylesheet" href="https://fonts.googleapis.com/css2?family=Open+Sans:wght@400;600;800&family=Roboto+Slab:wght@400;700;800&display=swap">
<style>
  :root {
    --orange: #f37122;
    --charcoal: #333333;
    --charcoal-deep: #2b2e2e;
    --white: #ffffff;
    --page: #e9e6e1;
  }
  * { margin: 0; padding: 0; box-sizing: border-box; }
  html, body { width: 1200px; height: 843px; overflow: hidden; background: var(--page); }
  .canvas { position: relative; width: 1200px; height: 843px; }

  .card {
    position: absolute; left: 300px; width: 600px; height: 343px;
    overflow: hidden; box-shadow: 0 6px 18px rgba(0,0,0,.25);
  }

  /* Services side */
  .card--services { top: 60px; background: var(--orange); }
  .services-mark {
    position: absolute; left: -70px; top: -80px; width: 330px; height: 330px;
    border-radius: 50%; background: var(--charcoal);
    display: flex; flex-direction: column; justify-content: center;
    padding-left: 110px; padding-top: 40px;
  }
  .services-mark__name {
    font-family: "Roboto Slab", serif; font-weight: 800; color: var(--orange);
    font-size: 40px; line-height: 1; text-transform: uppercase;
  }
  .services-list {
    position: absolute; right: 28px; top: 34px; width: 330px;
    text-align: right; color: var(--white);
    font-family: "Open Sans", sans-serif; font-size: 13px; line-height: 1.35;
  }
  .services-list h2 {
    font-size: 14.5px; font-weight: 800; text-transform: uppercase; line-height: 1.25;
    margin-top: 12px;
  }
  .services-list h2:first-child { margin-top: 0; }
  .services-list p { font-weight: 400; }

  /* Contact side */
  .card--contact { top: 443px; background: var(--charcoal-deep); }
  .contact-accent { position: absolute; inset: 0; }
  .contact-info {
    position: absolute; left: 36px; top: 36px; width: 250px; color: var(--white);
    font-family: "Roboto Slab", serif; font-size: 14px; line-height: 1.55;
  }
  .contact-info__name { color: var(--orange); font-weight: 700; font-size: 21px; text-transform: uppercase; line-height: 1.2; }
  .contact-info__title { font-size: 14px; margin-bottom: 8px; text-transform: uppercase; }
  .contact-info__row { display: flex; align-items: center; gap: 9px; white-space: nowrap; }
  .contact-info__row svg { width: 12px; height: 12px; flex: none; fill: var(--orange); }
  .contact-info__address { margin-top: 4px; }

  .brand {
    position: absolute; left: 300px; top: 60px; width: 310px; height: 310px;
    border-radius: 50%; background: var(--white);
    display: flex; align-items: center; justify-content: center; gap: 12px;
    padding: 0 36px 40px;
  }
  .brand__dot { width: 44px; height: 44px; border-radius: 50%; background: var(--orange); flex: none; }
  .brand__name {
    font-family: "Roboto Slab", serif; font-weight: 800; color: var(--charcoal);
    font-size: 20px; line-height: 1.1; text-transform: uppercase;
  }
</style>
</head>
<body>
<main class="canvas">

  <section class="card card--services" aria-label="Services side">
    <div class="services-mark">
      <span class="services-mark__name">Granite<br>Rim</span>
    </div>
    <div class="services-list">
      <h2>Specializing in new and<br>used tires &amp; wheels for</h2>
      <p>Loaders • Skid Steers • Telehandlers •<br>Boom Lifts • Forklifts and more •</p>
      <h2>Eliminating downtime</h2>
      <p>Wheel Exchange Program for New &amp;<br>Used Foam Filled &amp; Solid Rubber Tires</p>
      <h2>Specialty services</h2>
      <p>Foam Filling Tires •<br>Largest Tire Press in SE •<br>ONSITE Forklift Tire Press •<br>Boom Truck Services • Rubber Tracks •</p>
    </div>
  </section>

  <section class="card card--contact" aria-label="Contact side">
    <svg class="contact-accent" viewBox="0 0 600 343" aria-hidden="true">
      <polygon points="360,343 470,110 600,100 600,343" fill="var(--orange)"/>
    </svg>

    <div class="contact-info">
      <div class="contact-info__name">Dale Mercer</div>
      <div class="contact-info__title">CEO/Founder</div>
      <div class="contact-info__row"><svg viewBox="0 0 12 12"><path d="M2 1h3l1 3-1.5 1a6 6 0 0 0 2.5 2.5L8 6l3 1v3a1 1 0 0 1-1 1A9 9 0 0 1 1 2a1 1 0 0 1 1-1z"/></svg>844-GR-WHEEL</div>
      <div class="contact-info__row"><svg viewBox="0 0 12 12"><rect x="3" y="0.5" width="6" height="11" rx="1"/></svg>836 517 2290</div>
      <div class="contact-info__row"><svg viewBox="0 0 12 12"><rect x="1" y="4" width="10" height="6" rx="1"/><rect x="3" y="1" width="6" height="3"/></svg>561-278-9053</div>
      <div class="contact-info__row"><svg viewBox="0 0 12 12"><circle cx="6" cy="6" r="5.5"/></svg>dale@granite-example.com</div>
      <div class="contact-info__row"><svg viewBox="0 0 12 12"><circle cx="6" cy="6" r="5.5"/></svg>graniterimsupply-example.com</div>
      <div class="contact-info__address">5126 Marston Lane<br>Lake Harlow, FL 33498</div>
    </div>

    <div class="brand">
      <span class="brand__dot"></span>
      <span class="brand__name">Granite Rim<br>Supply LLC</span>
    </div>
  </section>

</main>
</body>
</html>
```